wealth management firm, professional group, new model

we have a logo that works but we need a card, white background using our colors...clean look

our tag line if can be used in

Steady Steps From Saver to Investor

```html
<!DOCTYPE html>
<html lang="en">
<head>
<meta charset="utf-8">
<title>Keelan Wealth Partners – Business Card</title>
<link href="https://fonts.googleapis.com/css2?family=Montserrat:wght@300;400;500&display=swap" rel="stylesheet">
<style>
  :root {
    --navy: #1b2a5c;
    --navy-deep: #13204a;
    --navy-light: #22346e;
    --ink: #2b3a66;
    --text-grey: #4a4f5e;
    --paper: #ffffff;
    --backdrop: #eceef2;
  }
  * { box-sizing: border-box; margin: 0; padding: 0; }
  html, body {
    width: 1200px;
    height: 800px;
    overflow: hidden;
    background: var(--backdrop);
    font-family: "Montserrat", sans-serif;
  }
  .stage {
    width: 1200px;
    height: 800px;
    display: flex;
    align-items: center;
    justify-content: center;
    gap: 60px;
  }
  .card {
    width: 525px;
    height: 300px;
    position: relative;
    box-shadow: 0 10px 30px rgba(20, 30, 60, 0.12);
  }
  .card-front {
    background: var(--paper);
    color: var(--ink);
  }
  .brand {
    position: absolute;
    top: 62px;
    right: 62px;
    text-align: center;
  }
  .brand-row {
    display: flex;
    align-items: center;
    gap: 14px;
    justify-content: center;
  }
  .brand-dot {
    width: 10px;
    height: 10px;
    border-radius: 50%;
    background: var(--ink);
  }
  .brand-name {
    font-weight: 400;
    font-size: 30px;
    letter-spacing: 0.42em;
    margin-right: -0.42em;
    color: var(--ink);
  }
  .brand-sub {
    margin-top: 8px;
    font-weight: 400;
    font-size: 10px;
    letter-spacing: 0.28em;
    color: var(--ink);
  }
  .contact {
    position: absolute;
    left: 42px;
    bottom: 40px;
    font-weight: 300;
    font-size: 11.5px;
    line-height: 1.65;
    color: var(--text-grey);
  }
  .contact .label {
    font-weight: 500;
    color: var(--ink);
  }
  .rule {
    width: 60px;
    height: 1px;
    background: var(--ink);
    margin: 6px 0 8px;
  }
  .tagline {
    font-weight: 300;
    font-size: 12.5px;
    color: var(--text-grey);
  }
  .card-back {
    background: var(--navy);
    overflow: hidden;
  }
  .back-pattern {
    position: absolute;
    inset: 0;
    width: 100%;
    height: 100%;
  }
  .back-name {
    position: absolute;
    inset: 0;
    display: flex;
    align-items: center;
    justify-content: center;
    color: var(--paper);
    font-weight: 400;
    font-size: 22px;
    letter-spacing: 0.42em;
    padding-left: 0.42em;
  }
</style>
</head>
<body>
  <main class="stage">
    <section class="card card-front">
      <div class="brand">
        <div class="brand-row">
          <span class="brand-dot"></span>
          <span class="brand-name">KEELAN</span>
        </div>
        <div class="brand-sub">WEALTH PARTNERS</div>
      </div>
      <div class="contact">
        <p><span class="label">T :</span> 03 5550 1827 <span class="label">E :</span> info@keelanmail.com</p>
        <p>Suite 4, 28 Harbour Lane, Carlton, VIC 4100</p>
        <p>www.keelanweb.com</p>
        <div class="rule"></div>
        <p class="tagline">Steady Steps From Saver to Investor</p>
      </div>
    </section>

    <section class="card card-back">
      <svg class="back-pattern" viewBox="0 0 525 300" preserveAspectRatio="none" role="img" aria-label="Embossed repeating brand pattern on navy">
        <defs>
          <linearGradient id="navyTone" x1="0" y1="0" x2="1" y2="1">
            <stop offset="0" stop-color="#22346e"/>
            <stop offset="0.55" stop-color="#1b2a5c"/>
            <stop offset="1" stop-color="#13204a"/>
          </linearGradient>
        </defs>
        <rect width="525" height="300" fill="url(#navyTone)"/>
      </svg>
      <div class="back-name">KEELAN</div>
    </section>
  </main>
</body>
</html>
```